Oil and Gas Exploration and Production company needs a business card design

We need a business card design using our logo and colors in the logo. We want a mainstream design.

```html
<!DOCTYPE html>
<html lang="en">
<head>
<meta charset="utf-8">
<title>Vireo Oil &amp; Gas — Business Card</title>
<link rel="stylesheet" href="https://fonts.googleapis.com/css2?family=Lato:wght@400;700&display=swap">
<style>
  :root {
    --page-bg: #ffffff;
    --card-bg: #ffffff;
    --ink: #111111;
    --text: #4a4a4a;
    --gold: #c99a2e;
    --rule: #d2d2d2;
  }
  * { box-sizing: border-box; margin: 0; padding: 0; }
  html, body {
    width: 1200px; height: 1200px; overflow: hidden;
    background: var(--page-bg);
    font-family: "Lato", Arial, sans-serif;
  }
  .card {
    position: absolute;
    left: 246px; top: 398px;
    width: 708px; height: 404px;
    background: var(--card-bg);
    border: 1px solid #ececec;
    overflow: hidden;
  }
  .brand {
    position: absolute;
    right: 40px; top: 62px;
    display: flex; align-items: center; gap: 12px;
  }
  .brand-dot {
    width: 34px; height: 34px; border-radius: 50%;
    background: var(--gold);
  }
  .brand-name {
    font-weight: 700; font-size: 40px; color: var(--ink);
    letter-spacing: -0.5px; line-height: 1;
  }
  .tab {
    position: absolute; left: 0; top: 210px;
    width: 27px; height: 74px;
    background: var(--gold);
    border-radius: 0 37px 37px 0;
  }
  .person-name {
    position: absolute; left: 38px; top: 226px;
    font-weight: 700; font-size: 27px; color: var(--ink);
    line-height: 1;
  }
  .person-title {
    position: absolute; left: 39px; top: 261px;
    font-weight: 700; font-size: 16px; color: var(--gold);
    line-height: 1;
  }
  .divider {
    position: absolute; left: 133px; right: 40px; top: 269px;
    height: 2px; background: var(--rule);
  }
  .contacts {
    position: absolute; left: 40px; top: 298px;
    list-style: none;
  }
  .contacts li {
    display: flex; align-items: center; gap: 9px;
    height: 25px;
    font-size: 17px; color: var(--text);
  }
  .contacts svg { width: 13px; height: 13px; flex: none; }
  .contacts .accent { color: var(--gold); }
  .address {
    position: absolute; right: 40px; top: 323px;
    text-align: right; font-size: 17px; color: var(--text);
    line-height: 25px; font-style: normal;
  }
</style>
</head>
<body>
  <div class="card">
    <div class="brand">
      <span class="brand-dot"></span>
      <span class="brand-name">Vireo Oil &amp; Gas</span>
    </div>

    <div class="tab"></div>
    <h1 class="person-name">Daniel Hart</h1>
    <p class="person-title">President</p>
    <div class="divider"></div>

    <ul class="contacts">
      <li>
        <svg viewBox="0 0 24 24" aria-hidden="true"><path fill="#c99a2e" d="M6.6 10.8a15.1 15.1 0 0 0 6.6 6.6l2.2-2.2c.3-.3.7-.4 1-.2 1.1.4 2.3.6 3.6.6.6 0 1 .4 1 1V20c0 .6-.4 1-1 1A17 17 0 0 1 3 4c0-.6.4-1 1-1h3.5c.6 0 1 .4 1 1 0 1.3.2 2.5.6 3.6.1.3 0 .7-.2 1z"/></svg>
        <span>(08) 5550 1472</span>
      </li>
      <li>
        <svg viewBox="0 0 24 24" aria-hidden="true"><rect x="2" y="5" width="20" height="14" rx="1" fill="#c99a2e"/><path d="M2.5 6l9.5 7 9.5-7" fill="none" stroke="#fff" stroke-width="1.8"/></svg>
        <span>hello@vireomail.com</span>
      </li>
      <li>
        <svg viewBox="0 0 24 24" aria-hidden="true"><g fill="none" stroke="#c99a2e" stroke-width="1.8"><circle cx="12" cy="12" r="9.5"/><ellipse cx="12" cy="12" rx="4" ry="9.5"/><path d="M2.5 12h19M4 7h16M4 17h16"/></g></svg>
        <span>www.<span class="accent">vireoenergy</span>.com</span>
      </li>
    </ul>

    <address class="address">
      Unit 4/58 Harbour Rd<br>
      Port Kellan SA 5600
    </address>
  </div>
</body>
</html>
```